Business Card Design

We have recently seen two business cards that caught our attention and think the designs would work for us. We are an accounting firm that serves small businesses in a variety of industries. Attached are the two business card that inspired us along with very rough layouts. We would like to see a professional layout using our company information.

Industry/Entity Type

Accounting

Contact Information for Business Card

Company Name - Marlowe Thistle
Address - 4182 Orlanby Lane, Suite 610, Houston, TX 77093
713-555-0187 - Main
281-555-0342 - Fax

Team Member Names, emails and phone numbers (see attachment)

```html
<!DOCTYPE html>
<html lang="en">
<head>
<meta charset="UTF-8">
<title>Marlowe Thistle – Business Card</title>
<link href="https://fonts.googleapis.com/css2?family=Lato:wght@400;700;900&display=swap" rel="stylesheet">
<style>
  :root {
    --page-bg: #2b2b2b;
    --card-light: #ffffff;
    --card-shade: #e4e4e4;
    --band: #0a0a0a;
    --ink: #111111;
    --muted: #9a9a9a;
    --on-band: #ffffff;
  }
  * { margin: 0; padding: 0; box-sizing: border-box; }
  html, body {
    width: 1200px; height: 900px; overflow: hidden;
    background: var(--page-bg);
    font-family: "Lato", sans-serif;
    color: var(--ink);
  }
  .business-card {
    position: absolute; left: 100px; top: 164px;
    width: 1000px; height: 572px;
    border-radius: 34px; overflow: hidden;
    background: linear-gradient(160deg, var(--card-light) 0%, #f3f3f3 50%, var(--card-shade) 100%);
    box-shadow: 0 20px 50px rgba(0,0,0,.55);
  }
  .brand-band {
    height: 96px; background: var(--band);
    display: flex; align-items: center; justify-content: center;
  }
  .brand-band h1 {
    color: var(--on-band); font-weight: 900; font-size: 42px; letter-spacing: 1px;
  }
  .brand-mark {
    position: absolute; left: 70px; top: 230px;
    display: flex; align-items: center; gap: 18px;
  }
  .brand-mark .mark-square { width: 34px; height: 34px; background: var(--ink); }
  .brand-mark span { font-weight: 900; font-size: 44px; color: var(--ink); letter-spacing: .5px; }
  .staff-block {
    position: absolute; right: 60px; top: 140px; text-align: right;
  }
  .staff-name { font-weight: 900; font-size: 34px; letter-spacing: .5px; line-height: 1.05; }
  .staff-title { font-weight: 400; font-size: 22px; color: var(--muted); letter-spacing: 1.5px; line-height: 1.1; }
  .contact-line {
    display: flex; align-items: center; justify-content: flex-end; gap: 8px;
    font-size: 24px; font-weight: 400; line-height: 1.35; margin-top: 2px;
  }
  .contact-line + .contact-line { margin-top: 0; }
  .contact-pair { display: flex; gap: 22px; justify-content: flex-end; }
  .icon { width: 22px; height: 22px; flex: none; fill: var(--ink); }
  .office-block { position: absolute; left: 70px; bottom: 52px; }
  .office-block .contact-line { justify-content: flex-start; font-size: 28px; }
  .office-fax { position: absolute; left: 440px; top: 395px; }
  .office-fax .contact-line { justify-content: flex-start; font-size: 28px; }
</style>
</head>
<body>
  <article class="business-card">
    <header class="brand-band"><h1>MARLOWE THISTLE</h1></header>

    <div class="brand-mark">
      <div class="mark-square"></div>
      <span>Marlowe Thistle</span>
    </div>

    <section class="staff-block">
      <div class="staff-name">DELPHINE ARROWAY</div>
      <div class="staff-title">ACCOUNT MANAGER</div>
      <div class="contact-line">
        <svg class="icon" viewBox="0 0 24 24"><path d="M4 7c0-1 1-2 2-2h12c1 0 2 1 2 2v2h-4V7H8v2H4zM7 10h10l3 9H4z"/></svg>
        713-555-0187
      </div>
      <div class="contact-line">
        <svg class="icon" viewBox="0 0 24 24"><rect x="6" y="2" width="12" height="20" rx="2" fill="none" stroke="#111" stroke-width="2"/></svg>
        832-555-0129
      </div>
      <div class="contact-line">
        <svg class="icon" viewBox="0 0 24 24"><path d="M2 5h20v14H2z"/><path d="M2 5l10 8 10-8" fill="none" stroke="#fff" stroke-width="1.6"/></svg>
        darroway@marlowethistle.com
      </div>
    </section>

    <div class="office-fax">
      <div class="contact-line">
        <svg class="icon" viewBox="0 0 24 24"><path d="M7 3h10v5H7z"/><path d="M3 9h18v8h-3v-3H6v3H3z"/><path d="M7 15h10v6H7z"/></svg>
        281-555-0342
      </div>
    </div>

    <section class="office-block">
      <div class="contact-line">
        <svg class="icon" viewBox="0 0 24 24"><path d="M4 7c0-1 1-2 2-2h12c1 0 2 1 2 2v2h-4V7H8v2H4zM7 10h10l3 9H4z"/></svg>
        713-555-0187
      </div>
      <div class="contact-line">
        <svg class="icon" viewBox="0 0 24 24"><path d="M12 3l10 9h-3v9h-5v-6h-4v6H5v-9H2z"/></svg>
        4182 Orlanby Lane, Suite 610, Houston, TX 77093
      </div>
    </section>
  </article>
</body>
</html>
```